Business Cards for a law firm

Business cards for our law firm. Use our silhoette logo and OAK PARTNERS - check our website (www.oakpartners.example)

Contact Information for Business Card

our silhouette logo, OAK PARTNERS, 800-555-0147, Dorian Pemberton, dorian@oakpartners.example

Requirements
Must have
• our silhouette logo, OAK PARTNERS, 800-555-0147, Dorian Pemberton, dorian@oakpartners.example

```html
<!DOCTYPE html>
<html lang="en">
<head>
<meta charset="utf-8">
<title>Oak Partners Business Card</title>
<link href="https://fonts.googleapis.com/css2?family=Montserrat:wght@400;500;600;700&display=swap" rel="stylesheet">
<style>
  :root {
    --navy: #22326b;
    --ink: #1d1d1f;
    --paper: #ffffff;
    --backdrop: #e9e7e3;
    --figure-light: #dfe3ee;
  }
  html, body {
    margin: 0;
    padding: 0;
    width: 900px;
    height: 1200px;
    overflow: hidden;
    background: var(--backdrop);
    font-family: "Montserrat", Arial, sans-serif;
  }
  .canvas {
    position: relative;
    width: 900px;
    height: 1200px;
  }
  .card {
    position: absolute;
    border-radius: 22px;
    overflow: hidden;
    box-shadow: 0 6px 14px rgba(0, 0, 0, 0.25);
  }
  .card-front {
    left: 80px; top: 131px; width: 742px; height: 440px;
    background: var(--paper);
  }
  .card-back {
    left: 78px; top: 638px; width: 744px; height: 440px;
    background: var(--navy);
  }
  .wordmark {
    position: absolute;
    margin: 0;
    font-weight: 600;
    letter-spacing: 0.06em;
    white-space: nowrap;
  }
  .card-front .wordmark {
    left: 54px; top: 64px;
    font-size: 27px;
    color: var(--navy);
  }
  .card-back .wordmark {
    left: 0; right: 0; top: 204px;
    text-align: center;
    font-size: 44px;
    color: var(--paper);
  }
  .holder-name {
    position: absolute;
    left: 46px; top: 190px;
    margin: 0;
    font-size: 26px;
    font-weight: 700;
    color: var(--navy);
  }
  .holder-role {
    position: absolute;
    left: 46px; top: 225px;
    margin: 0;
    font-size: 16px;
    color: var(--ink);
  }
  .address {
    position: absolute;
    left: 45px; top: 263px;
    margin: 0;
    font-style: normal;
    font-size: 16px;
    line-height: 20px;
    color: var(--ink);
  }
  .contact-list {
    position: absolute;
    left: 45px; top: 319px;
    margin: 0; padding: 0;
    list-style: none;
    font-size: 16px;
    color: var(--ink);
  }
  .contact-list li {
    display: flex;
    align-items: center;
    height: 28px;
  }
  .contact-list svg {
    width: 16px; height: 16px;
    margin-right: 8px;
    fill: var(--navy);
  }
  .figure-art {
    position: absolute;
    left: 442px; top: 50px;
    width: 264px; height: 390px;
    background: linear-gradient(180deg, var(--figure-light), #c3cadd);
    border-radius: 10px 10px 0 0;
  }
</style>
</head>
<body>
<main class="canvas">
  <section class="card card-front">
    <p class="wordmark">OAK PARTNERS</p>
    <h1 class="holder-name">Dorian Pemberton</h1>
    <p class="holder-role">Lawyer</p>
    <address class="address">418 Maple Grove Rd, #210<br>Fairbrook, OH 430091</address>
    <ul class="contact-list">
      <li>
        <svg viewBox="0 0 24 24" aria-hidden="true"><path d="M6.6 10.8a15.1 15.1 0 0 0 6.6 6.6l2.2-2.2c.3-.3.7-.4 1-.2 1.1.4 2.3.6 3.6.6.6 0 1 .4 1 1V20c0 .6-.4 1-1 1A17 17 0 0 1 3 4c0-.6.4-1 1-1h3.5c.6 0 1 .4 1 1 0 1.3.2 2.5.6 3.6.1.3 0 .7-.2 1z"/></svg>
        800-555-0147
      </li>
      <li>
        <svg viewBox="0 0 24 24" aria-hidden="true"><path d="M3 6h18v12H3z" opacity="0"/><path d="M3 6l9 6 9-6v12H3z"/><path d="M3 5h18l-9 6z"/></svg>
        dorian@oakpartners.example
      </li>
      <li>
        <svg viewBox="0 0 24 24" aria-hidden="true"><circle cx="12" cy="12" r="10"/></svg>
        www.oakpartners.example
      </li>
    </ul>
    <div class="figure-art" role="img" aria-label="Silhouette illustration of two men in suits standing side by side"></div>
  </section>

  <section class="card card-back">
    <p class="wordmark">OAK PARTNERS</p>
  </section>
</main>
</body>
</html>
```